'Little Lantern' promotional brochure

We have designed a 6 week program to educate impending first-time parents about the things they need to know to survive the first 6 months. Sessions delivered by general practitioner/family doctor, dietician, physiotherapist, speech pathologist and psychologist. Our promotional blurb is: 'A comprehensive education program for first-time parents-to-be, delivered over 6 weeks by health professionals in your community, about everything you need to know to look after your baby (and yourself!) in the first 6 months'. I now want to put together a promotional brochure to be distributed to those couples who express an interest which will provide further details of what will be delivered in the course.
Updates
In terms of layout, I envisaged a double sided A4 size, foldable into 3 sections, but very happy to be guided on this.
Target Market(s)
To appeal to a young, well educated demographic. First time parents couples.
Industry/Entity Type
Medical
Font styles to use
Other font styles liked:
- Playfair Display
Requirements
Must have
- Playfair display font to be consistent with our logo (attached). Logo also included please. Some consistency with colours of logo please.
Nice to have
- I am a doctor, and have no creative genes! But prefer a clean and professional appearance overall. Not too cluttered in overall appearance.
Should not have
- No cheesy pictures of babies.

```html
<!DOCTYPE html>
<html lang="en">
<head>
<meta charset="utf-8">
<title>Little Lantern – Trifold Brochure</title>
<link href="https://fonts.googleapis.com/css2?family=Playfair+Display:ital,wght@0,400;0,700;1,400&display=swap" rel="stylesheet">
<style>
  :root {
    --green: #7cc05c;
    --green-deep: #6bb34b;
    --panel: #eeefee;
    --paper: #f6f6f5;
    --road-light: #e2e4e3;
    --road-dark: #c4c8c6;
    --ink: #3b3b3b;
    --ink-soft: #7d7f7e;
    --white: #ffffff;
    --stage: #dfe1e0;
  }
  * { box-sizing: border-box; margin: 0; padding: 0; }
  html, body { width: 1200px; height: 900px; overflow: hidden; }
  body {
    background: var(--stage);
    font-family: "Playfair Display", Georgia, serif;
    color: var(--ink);
    position: relative;
  }
  .spread {
    position: absolute;
    top: 240px;
    width: 585px;
    height: 420px;
    display: flex;
    box-shadow: 0 6px 18px rgba(0,0,0,.12);
    overflow: hidden;
  }
  .spread--outside { left: 10px; }
  .spread--inside  { left: 605px; }
  .panel {
    position: relative;
    width: 195px;
    height: 100%;
    background: var(--panel);
    border-right: 1px solid rgba(0,0,0,.05);
    overflow: hidden;
  }
  .panel:last-child { border-right: 0; }

  /* Outside: green info panel */
  .panel--info {
    background: var(--green);
    color: var(--white);
    text-align: center;
    text-transform: uppercase;
    padding: 50px 18px 0;
    font-size: 9px;
    line-height: 1.4;
  }
  .rule { width: 62px; height: 2px; background: currentColor; margin: 30px auto; }
  .panel--info strong { font-weight: 700; }
  .price { font-size: 16px; line-height: 1.35; font-weight: 700; margin-top: 6px; }

  /* Outside: contact panel */
  .panel--contact { padding: 56px 20px 0; }
  .contact-label { font-size: 8px; font-weight: 700; text-transform: uppercase; line-height: 1.35; }
  .contact-phone { font-size: 13px; margin-top: 2px; }
  .panel--contact .rule { background: var(--green); width: 50px; margin: 76px auto 0; }
  .panel--contact .brand { position: absolute; left: 28px; bottom: 98px; }

  /* Brand lockup */
  .brand { display: flex; align-items: center; gap: 7px; }
  .brand-mark { width: 22px; height: 22px; background: var(--green); flex: none; }
  .brand-name { color: var(--green); font-size: 12px; line-height: 1.05; font-weight: 400; text-transform: uppercase; }

  /* Outside: cover */
  .panel--cover { background: var(--paper); }
  .cover-frame { position: absolute; inset: 10px; border: 2px solid var(--green); }
  .cover-frame .brand { position: absolute; top: 34px; left: 26px; }
  .cover-frame .rule { position: absolute; top: 84px; left: 50%; margin: 0 0 0 -28px; width: 56px; background: var(--green); }
  .cover-title {
    position: absolute; top: 104px; left: 0; right: 0;
    text-align: center; color: var(--green-deep);
    font-size: 17px; font-weight: 700; text-transform: uppercase; letter-spacing: .3px;
  }
  .cover-sub {
    position: absolute; top: 128px; left: 12px; right: 12px;
    text-align: center; color: var(--ink-soft);
    font-size: 8px; line-height: 1.3; text-transform: uppercase;
  }
  .cover-photo {
    position: absolute; left: 0; right: 0; bottom: 0; height: 168px;
    border-top: 2px solid var(--green);
    background: linear-gradient(160deg, #e9edf0 0%, #c9ccd0 45%, #d8b9a2 70%, #7d8c9a 100%);
  }

  /* Inside */
  .green-block {
    position: absolute; left: 0; right: 0;
    background: var(--green); color: var(--white);
    font-size: 8px; line-height: 1.36;
    padding: 11px 12px;
  }
  .copy { position: absolute; left: 12px; right: 12px; font-size: 8px; line-height: 1.36; }
  .copy p + p, .green-block p + p { margin-top: 6px; }
  .topic-list { list-style: none; }
  .topic-list li::before { content: "*"; }

  .route-art {
    position: absolute; left: 0; right: 0;
    background: linear-gradient(90deg, var(--road-light) 0%, var(--road-dark) 50%, var(--road-light) 100%);
  }

  .gb-week1 { top: 0; height: 158px; }
  .route-art--left { top: 160px; height: 62px; }
  .copy-week2 { top: 230px; }

  .copy-week3 { top: 10px; }
  .route-art--middle { top: 228px; height: 40px; }
  .gb-week4 { top: 270px; bottom: 0; }

  .panel--inside-right .brand { position: absolute; top: 16px; left: 40px; }
  .gb-week5 { top: 56px; height: 110px; }
  .route-art--right { top: 168px; height: 70px; }
  .copy-week6 { top: 246px; }
</style>
</head>
<body>

<section class="spread spread--outside" aria-label="Brochure outside">
  <div class="panel panel--info">
    <p>Delivered over 6 weeks by health professionals in your comunity</p>
    <div class="rule"></div>
    <p>Everything you need to know to look after your baby (and yourself)<br><strong>in the first 6 months</strong></p>
    <div class="rule"></div>
    <p class="price">Total cost<br>$300</p>
  </div>

  <div class="panel panel--contact">
    <p class="contact-label">Contact details for enquiries/bookings</p>
    <p class="contact-phone">(02) 5550 1234</p>
    <div class="rule"></div>
    <div class="brand">
      <span class="brand-mark"></span>
      <span class="brand-name">Wattlebrook<br>Health</span>
    </div>
  </div>

  <div class="panel panel--cover">
    <div class="cover-frame">
      <div class="brand">
        <span class="brand-mark"></span>
        <span class="brand-name">Wattlebrook<br>Health</span>
      </div>
      <div class="rule"></div>
      <h1 class="cover-title">Little Lantern</h1>
      <p class="cover-sub">A comprehensive education program for first-time parents</p>
      <div class="cover-photo" role="img" aria-label="Photo of a young couple holding their baby"></div>
    </div>
  </div>
</section>

<section class="spread spread--inside" aria-label="Brochure inside">
  <div class="panel panel--inside-left">
    <div class="green-block gb-week1">
      <p>GP Dr Maren Holloway will share information for Mum's own health after delivery.</p>
      <p>Topics include:</p>
      <ul class="topic-list">
        <li>Vaccinations in pregnancy</li>
        <li>Bleeding, bladder and bowel after delivery</li>
        <li>Breastfeeding, engorgement and mastitis</li>
        <li>Bottle feeding</li>
        <li>Post-natal anxiety &amp; depression</li>
        <li>Intimacy and contraception</li>
      </ul>
    </div>
    <div class="route-art route-art--left" role="img" aria-label="Winding road illustration with icon markers for week 1 and week 2"></div>
    <div class="copy copy-week2">
      <p>Session 1 – Clinical Psychologist Dr Tessa Varga will discuss changes in relationships as couples become parents, gender roles in parenting and post-natal depression.</p>
      <p>Session 2 – Physiotherapist Corinne Ashby will present advice for Mums regarding exercise during and after pregnancy, looking after the pelvic floor during and after pregnancy, and abdominal muscle separation management. She will also provide advice for promoting babies' neck strength and minimising the risk of flat spots on the head and encouraging gross motor skills in the first 6 months.</p>
    </div>
  </div>

  <div class="panel panel--inside-middle">
    <div class="copy copy-week3">
      <p>Session 1 – Dietician Nina Calder provides advice for Mums regarding healthy eating during pregnancy and lactation, normal weight gain during pregnancy and realistic weight loss after. She will also discuss the evidence regarding breastfeeding vs bottle-feeding, normal infant weight gain and introducing solids (including those with potential for allergy).</p>
      <p>Session 2 – Paediatric Speech Pathologist Priya Ellison will share information about latching and breast-feeding troubles (e.g. tongue-tie), advice about dummies and finger-sucking, introducing solids &amp; feeding (including 'touch' foods), encouraging language development and current evidence about electronic devices impacting language development.</p>
    </div>
    <div class="route-art route-art--middle" role="img" aria-label="Winding road illustration with icon markers for week 3 and week 4"></div>
    <div class="green-block gb-week4">
      <p>GP Dr Maren Holloway will share advice about your babies' health in the first 6 months, including:</p>
      <ul class="topic-list">
        <li>Skin of newborns</li>
        <li>Sleeping</li>
        <li>Crying</li>
        <li>Immunisations</li>
        <li>Fever and infections</li>
        <li>Diarrhoea and constipation</li>
        <li>Teething</li>
        <li>Understanding a baby's signals</li>
      </ul>
    </div>
  </div>

  <div class="panel panel--inside-right">
    <div class="brand">
      <span class="brand-mark"></span>
      <span class="brand-name">Wattlebrook<br>Health</span>
    </div>
    <div class="green-block gb-week5">
      <p>Session 1 – Clinical Psychologist Dr Tessa Varga will share information about bonding &amp; attachment with your baby, how to promote their social &amp; emotional development and how to manage separation anxiety. She will also discuss positive parenting approaches.</p>
    </div>
    <div class="route-art route-art--right" role="img" aria-label="Winding road illustration with icon markers for week 5 and week 6"></div>
    <div class="copy copy-week6">
      <p>Session 1 – Secret Men's Business – a men-only session (including beer!) with a new father for frank discussion about the road ahead. Mums will do a shopping excursion with the GP &amp; Dietician to Freshway to look at baby products and food – the good and the bad!</p>
      <p>Session 2 – Program review, reflection and evaluation and future session planning when baby is 6 months of age.</p>
    </div>
  </div>
</section>

</body>
</html>
```